Homemaking training schools needs a Business Card design

Designer, Hello!

No special requirements, good-looking enough.
--------------------------------------------------------------------------

Name: Marcus Dole
Chairman
Tel: 0574-71948263
Mobile: 13857420916
Email: kelvora@mailnest.example
Web: www.prt2019.example
Add: No.258, LanpingJie, BeiyuanQu, Ningbo, Zhejiang

LOGO
Ningbo PRT Homemaking Training School

Target Market(s)

pregnant women, mothers, infants, the elderly and families, including cleaning, cooking, nursing training.

Industry/Entity Type

Business

Contact Information for Business Card

Name: Marcus Dole
Chairman
Tel: 0574-71948263
Mobile: 13857420916
Email: kelvora@mailnest.example
Web: www.prt2019.example

LOGO

Font styles to use
Serif
Sans Serif
Decorative

Requirements
Nice to have
• Feels: clean, specifications, safety, comfort, warmth and happiness.

```html
<!DOCTYPE html>
<html lang="en">
<head>
<meta charset="UTF-8">
<title>PinRuiTang Business Card</title>
<link rel="stylesheet" href="https://fonts.googleapis.com/css2?family=Montserrat:wght@400;500;700;800&display=swap">
<style>
  :root {
    --page: #2b2b2b;
    --card: #060606;
    --blue: #1677c0;
    --pink: #ec0b8f;
    --white: #ffffff;
  }
  * { margin: 0; padding: 0; box-sizing: border-box; }
  html, body { width: 1200px; height: 900px; overflow: hidden; }
  body {
    background: var(--page);
    font-family: "Montserrat", sans-serif;
    display: flex;
    flex-direction: column;
    align-items: center;
    justify-content: center;
    gap: 44px;
  }
  .card {
    width: 660px;
    height: 378px;
    background: var(--card);
    position: relative;
    box-shadow: 0 12px 30px rgba(0,0,0,0.45);
  }
  /* front */
  .card-front .brand-block {
    position: absolute;
    left: 150px;
    top: 118px;
    width: 400px;
    text-align: center;
  }
  .brand-name {
    color: var(--blue);
    font-weight: 700;
    font-size: 50px;
    letter-spacing: -0.5px;
    line-height: 1;
    display: inline-flex;
    align-items: center;
    gap: 12px;
  }
  .brand-dot {
    width: 16px; height: 16px;
    border-radius: 50%;
    background: var(--pink);
    display: inline-block;
  }
  .tagline {
    display: flex;
    align-items: center;
    gap: 12px;
    color: var(--white);
    font-size: 19px;
    font-weight: 400;
    margin-top: 12px;
    white-space: nowrap;
  }
  .tagline::before, .tagline::after {
    content: "";
    flex: 1;
    height: 1.5px;
    background: var(--white);
  }
  .card-front .website {
    color: var(--white);
    font-weight: 700;
    font-size: 20px;
    margin-top: 14px;
    letter-spacing: 0.3px;
  }
  /* back */
  .decor-circle {
    position: absolute;
    left: 90px;
    top: 95px;
    width: 170px;
    height: 170px;
    border-radius: 50%;
    background: var(--blue);
  }
  .card-back .brand-block {
    position: absolute;
    left: 330px;
    top: 58px;
    width: 280px;
    text-align: center;
  }
  .card-back .brand-name { font-size: 33px; gap: 8px; }
  .card-back .brand-dot { width: 11px; height: 11px; }
  .card-back .tagline { font-size: 13px; margin-top: 8px; gap: 8px; }
  .person {
    position: absolute;
    left: 330px;
    top: 148px;
  }
  .person-name {
    color: var(--blue);
    font-weight: 800;
    font-size: 25px;
    letter-spacing: 0.5px;
    text-transform: uppercase;
  }
  .person-title {
    color: var(--white);
    font-weight: 700;
    font-size: 13px;
    letter-spacing: 0.6px;
    margin-top: 2px;
  }
  .address {
    color: var(--white);
    font-size: 13px;
    font-weight: 500;
    line-height: 1.45;
    margin-top: 14px;
  }
  .contact-list { list-style: none; margin-top: 10px; }
  .contact-list li {
    color: var(--white);
    font-size: 13px;
    font-weight: 500;
    display: flex;
    align-items: center;
    gap: 9px;
    line-height: 1.55;
  }
  .contact-list svg { width: 12px; height: 12px; flex: none; }
</style>
</head>
<body>
  <section class="card card-front">
    <div class="brand-block">
      <div class="brand-name"><span class="brand-dot"></span>PinRuiTang</div>
      <div class="tagline">Training &amp; Services</div>
      <div class="website">www.prt2019.example</div>
    </div>
  </section>

  <section class="card card-back">
    <div class="decor-circle"></div>
    <div class="brand-block">
      <div class="brand-name"><span class="brand-dot"></span>PinRuiTang</div>
      <div class="tagline">Training &amp; Services</div>
    </div>
    <div class="person">
      <div class="person-name">Marcus Dole</div>
      <div class="person-title">CHAIRMAN</div>
      <div class="address">No.258, LanpingJie,<br>BeiyuanQu, Ningbo, Zhejiang</div>
      <ul class="contact-list">
        <li>
          <svg viewBox="0 0 24 24" fill="var(--blue)"><path d="M6.6 10.8a15.1 15.1 0 0 0 6.6 6.6l2.2-2.2a1 1 0 0 1 1-.25 11.4 11.4 0 0 0 3.6.57 1 1 0 0 1 1 1V20a1 1 0 0 1-1 1A17 17 0 0 1 3 4a1 1 0 0 1 1-1h3.5a1 1 0 0 1 1 1c0 1.25.2 2.45.57 3.57a1 1 0 0 1-.25 1z"/></svg>
          0574-71948263
        </li>
        <li>
          <svg viewBox="0 0 24 24" fill="none" stroke="var(--blue)" stroke-width="2.4"><rect x="6" y="2" width="12" height="20" rx="2"/><line x1="10" y1="18" x2="14" y2="18"/></svg>
          13857420916
        </li>
        <li>
          <svg viewBox="0 0 24 24" fill="none" stroke="var(--blue)" stroke-width="2.4"><rect x="2" y="5" width="20" height="14" rx="1.5"/><polyline points="2,6 12,13 22,6"/></svg>
          kelvora@mailnest.example
        </li>
        <li>
          <svg viewBox="0 0 24 24" fill="none" stroke="var(--blue)" stroke-width="2.2"><circle cx="12" cy="12" r="10"/><ellipse cx="12" cy="12" rx="4.5" ry="10"/><line x1="2" y1="12" x2="22" y2="12"/></svg>
          www.prt2019.example
        </li>
      </ul>
    </div>
  </section>
</body>
</html>
```